Business Card Design

I already have a company logo for my company. I have a logo for the manufacturer we represent. I want a professional business card design.

```html
<!DOCTYPE html>
<html lang="en">
<head>
<meta charset="utf-8">
<title>Halvard Signal Works – Business Card</title>
<link href="https://fonts.googleapis.com/css2?family=Open+Sans:wght@400;600;700&display=swap" rel="stylesheet">
<style>
  :root {
    --backdrop: #3a3a3a;
    --card: #161616;
    --card-edge: #0c0c0c;
    --red: #e3232c;
    --white: #f2f2f2;
    --muted: #d6d6d6;
  }
  * { box-sizing: border-box; margin: 0; padding: 0; }
  html, body {
    width: 1200px; height: 780px; overflow: hidden;
    background: var(--backdrop);
    font-family: "Open Sans", Arial, sans-serif;
  }
  .canvas {
    width: 1200px; height: 780px;
    display: flex; align-items: center; justify-content: center; gap: 56px;
  }
  .card {
    position: relative;
    width: 520px; height: 300px;
    background: var(--card);
    border-radius: 26px;
    box-shadow: 0 6px 0 var(--card-edge), 0 18px 40px rgba(0,0,0,.45);
  }
  /* company name stand-in */
  .brand {
    display: flex; align-items: center; gap: 10px;
    color: var(--white); font-weight: 700; text-transform: uppercase;
    letter-spacing: .04em; line-height: 1;
  }
  .brand-square { background: var(--red); flex: none; }

  /* front */
  .card-front .brand { position: absolute; top: 62px; left: 150px; font-size: 22px; }
  .card-front .brand-square { width: 18px; height: 18px; }
  .person { position: absolute; left: 40px; top: 176px; text-align: right; width: 170px; }
  .person-name { color: var(--red); font-size: 19px; font-weight: 600; letter-spacing: .02em; }
  .person-title { color: var(--muted); font-size: 12.5px; margin-top: 3px; }
  .divider { position: absolute; left: 228px; top: 170px; width: 1.5px; height: 72px; background: var(--red); }
  .contacts { position: absolute; left: 246px; top: 168px; list-style: none; }
  .contacts li { display: flex; align-items: center; gap: 9px; color: var(--white); font-size: 14px; line-height: 26px; }
  .contacts svg { width: 13px; height: 13px; fill: var(--red); flex: none; }

  /* back */
  .card-back { display: flex; align-items: center; justify-content: center; }
  .card-back .brand { font-size: 30px; }
  .card-back .brand-square { width: 24px; height: 24px; }
</style>
</head>
<body>
<main class="canvas">
  <section class="card card-front" aria-label="Card front">
    <div class="brand"><span class="brand-square"></span>Halvard Signal Works LLC</div>
    <div class="person">
      <p class="person-name">MARCUS DALE</p>
      <p class="person-title">Managing Director</p>
    </div>
    <div class="divider"></div>
    <ul class="contacts">
      <li>
        <svg viewBox="0 0 24 24" aria-hidden="true"><path d="M6.6 10.8a15.1 15.1 0 0 0 6.6 6.6l2.2-2.2a1 1 0 0 1 1-.25 11.4 11.4 0 0 0 3.6.57 1 1 0 0 1 1 1V20a1 1 0 0 1-1 1A17 17 0 0 1 3 4a1 1 0 0 1 1-1h3.5a1 1 0 0 1 1 1c0 1.25.2 2.45.57 3.6a1 1 0 0 1-.25 1z"/></svg>
        555 014 2260
      </li>
      <li>
        <svg viewBox="0 0 24 24" aria-hidden="true"><path d="M2 5h20v14H2zm2 2v.5l8 5 8-5V7zm0 2.8V17h16V9.8l-8 5z"/></svg>
        info@halvardsignal.com
      </li>
      <li>
        <svg viewBox="0 0 24 24" aria-hidden="true"><path d="M12 2a10 10 0 1 0 0 20 10 10 0 0 0 0-20zm6.9 9h-3a15 15 0 0 0-1.3-6.1A8 8 0 0 1 18.9 11zM12 4.1c.9 1.3 1.8 3.6 1.9 6.9h-3.8c.1-3.3 1-5.6 1.9-6.9zM9.4 4.9A15 15 0 0 0 8.1 11h-3a8 8 0 0 1 4.3-6.1zM5.1 13h3a15 15 0 0 0 1.3 6.1A8 8 0 0 1 5.1 13zm6.9 6.9c-.9-1.3-1.8-3.6-1.9-6.9h3.8c-.1 3.3-1 5.6-1.9 6.9zm2.6-.8a15 15 0 0 0 1.3-6.1h3a8 8 0 0 1-4.3 6.1z"/></svg>
        www.halvardsignal.com
      </li>
    </ul>
  </section>

  <section class="card card-back" aria-label="Card back">
    <div class="brand"><span class="brand-square"></span>Halvard Signal Works LLC</div>
  </section>
</main>
</body>
</html>
```